Family Values Statement Image

I have created a statement of values for my family. Our last name is Pilwothy, and we are using those letters as an acronym. I would like an image with these words and letters with a tree with deep roots, where the roots are the focal point.

A - All In
N - Never Settle
D - Dependable
E - Enthusiastic
R - Repair
E - Enduring
G - Gushy Hearted
G - Gratitudes

Note that "gratitudes" is intentionally misspelled.

• On further reflection, I am interested in the words being much more prominent than the tree. In fact, the tree could be quite small or even just a watermark behind the words.

```html
<!DOCTYPE html>
<html lang="en">
<head>
<meta charset="utf-8">
<title>Pilwothy Family Values</title>
<link href="https://fonts.googleapis.com/css2?family=Poppins:wght@600;700;800&family=Great+Vibes&display=swap" rel="stylesheet">
<style>
  :root {
    --poster-bg: #0b0b0b;
    --initial: #ffffff;
    --word-light: #d2d2d2;
    --word-dark: #9a9492;
    --surname: #b9b9b9;
    --script: #6f6f6f;
    --heading: #d8d8d8;
    --tree-shade: #2a2a2a;
    --tree-icon: #9c9c9c;
  }
  * { margin: 0; padding: 0; box-sizing: border-box; }
  html, body { width: 1122px; height: 1200px; overflow: hidden; background: var(--poster-bg); }
  .poster {
    position: relative;
    width: 1122px;
    height: 1200px;
    overflow: hidden;
    background: var(--poster-bg);
    font-family: "Poppins", Arial, sans-serif;
  }
  .tree-watermark {
    position: absolute;
    left: 0;
    top: 470px;
    width: 455px;
    height: 730px;
    opacity: 0.55;
  }
  .tree-emblem {
    position: absolute;
    left: 815px;
    top: 62px;
    width: 225px;
    height: 160px;
  }
  .heading {
    position: absolute;
    left: 262px;
    top: 86px;
    font-size: 31px;
    font-weight: 600;
    color: var(--heading);
    letter-spacing: 0.5px;
    line-height: 1.2;
  }
  .family-script {
    position: absolute;
    left: 88px;
    top: 132px;
    font-family: "Great Vibes", cursive;
    font-size: 64px;
    color: var(--script);
    line-height: 1;
  }
  .surname {
    position: absolute;
    left: 48px;
    top: 226px;
    writing-mode: vertical-rl;
    font-size: 158px;
    font-weight: 800;
    line-height: 1;
    color: var(--surname);
    letter-spacing: -2px;
  }
  .values {
    position: absolute;
    left: 258px;
    top: 228px;
    list-style: none;
  }
  .value {
    font-size: 80px;
    font-weight: 700;
    line-height: 106px;
    letter-spacing: -1.5px;
    white-space: nowrap;
  }
  .value .initial { color: var(--initial); }
  .value .rest {
    background: linear-gradient(90deg, var(--word-light), var(--word-dark));
    -webkit-background-clip: text;
    background-clip: text;
    color: transparent;
  }
</style>
</head>
<body>
<main class="poster">
  <svg class="tree-watermark" role="img" aria-label="Faint tree with spreading branches and deep roots behind the letters" viewBox="0 0 455 730">
    <defs>
      <radialGradient id="shade" cx="0.35" cy="0.4" r="0.7">
        <stop offset="0" stop-color="#2a2a2a" stop-opacity="0.9"/>
        <stop offset="1" stop-color="#2a2a2a" stop-opacity="0"/>
      </radialGradient>
    </defs>
    <rect width="455" height="730" fill="url(#shade)"/>
  </svg>

  <svg class="tree-emblem" role="img" aria-label="Small tree emblem with leafy crown and roots" viewBox="0 0 225 160">
    <defs>
      <radialGradient id="emblem" cx="0.5" cy="0.45" r="0.55">
        <stop offset="0" stop-color="#9c9c9c"/>
        <stop offset="1" stop-color="#9c9c9c" stop-opacity="0.15"/>
      </radialGradient>
    </defs>
    <ellipse cx="112" cy="80" rx="108" ry="78" fill="url(#emblem)"/>
  </svg>

  <h1 class="heading">OUR FAMILY VALUES</h1>
  <div class="family-script">Pilwothy</div>

  <div class="surname">PILWOTHY</div>

  <ul class="values">
    <li class="value"><span class="initial">P</span><span class="rest">ull Together</span></li>
    <li class="value"><span class="initial">I</span><span class="rest">ntegrity</span></li>
    <li class="value"><span class="initial">L</span><span class="rest">oyal</span></li>
    <li class="value"><span class="initial">W</span><span class="rest">arm Hearted</span></li>
    <li class="value"><span class="initial">O</span><span class="rest">ptimistic</span></li>
    <li class="value"><span class="initial">T</span><span class="rest">hankful</span></li>
    <li class="value"><span class="initial">H</span><span class="rest">onest</span></li>
    <li class="value"><span class="initial">Y</span><span class="rest">oung At Heart</span></li>
  </ul>
</main>
</body>
</html>
```